Pet Sitting Business Card

Would like a business card designed for my new pet sitting business
Card needs to match with logo design.
Blue and Orange are the theme colours.

Simple yet sophisticated design

company name:- MEADOWLARK PET CARE
Dana Kovich
Owner
0452716093
dana@meadowlarkpetcare.com.au
www.meadowlarkpetcare.com.au

I'm going to close my deadline early. I will be picking a winner by the 10th of May. Please submit designs before then.
thank you

Target Market(s)

All types of professional pet lovers wishing to have their pet looked after

Industry/Entity Type

Pet

Requirements
Must have
• Logo design
Blue and orange

```html
<!DOCTYPE html>
<html lang="en">
<head>
<meta charset="utf-8">
<title>Meadowlark Pet Care – Business Card</title>
<link rel="stylesheet" href="https://fonts.googleapis.com/css2?family=Michroma&display=swap">
<style>
  :root {
    --bg: #2b2b2d;
    --card: #ececec;
    --blue: #2490e6;
    --blue-light: #55c4f2;
    --orange: #ef8a22;
    --ink: #3a3a3a;
    --white: #ffffff;
  }
  * { box-sizing: border-box; margin: 0; padding: 0; }
  html, body {
    width: 1200px; height: 900px; overflow: hidden;
    background: var(--bg);
    font-family: "Michroma", "Helvetica Neue", Arial, sans-serif;
  }
  .canvas { position: relative; width: 1200px; height: 900px; }
  .card {
    position: absolute; left: 250px; width: 700px; height: 400px;
    background: var(--card); border-radius: 22px; overflow: hidden;
  }
  .card--back { top: 40px; }
  .card--front { top: 460px; }
  .card-band { position: absolute; inset: 0; width: 700px; height: 400px; }
  .band-text {
    position: absolute; color: var(--white); font-size: 15px;
    letter-spacing: 2px; text-transform: uppercase;
  }
  .band-text--web { left: 34px; top: 34px; text-transform: none; letter-spacing: 1px; }
  .band-text--title { left: 0; right: 0; top: 36px; text-align: center; }
  .brand {
    position: absolute; left: 0; right: 0; text-align: center;
  }
  .card--back .brand { top: 230px; }
  .card--front .brand { top: 195px; }
  .brand-name {
    color: var(--blue); font-size: 30px; letter-spacing: 1px; line-height: 1.2;
  }
  .contacts {
    position: absolute; left: 40px; right: 40px; top: 275px;
    color: var(--ink); font-size: 13px; letter-spacing: 1px;
    display: flex; flex-direction: column; align-items: center; gap: 10px;
  }
  .contact-row { display: flex; gap: 22px; align-items: center; }
  .contact { display: flex; align-items: center; gap: 7px; white-space: nowrap; }
  .contact-icon { width: 18px; height: 18px; flex: none; }
</style>
</head>
<body>
<main class="canvas">

  <section class="card card--back" aria-label="Card back">
    <svg class="card-band" viewBox="0 0 700 400" aria-hidden="true">
      <defs>
        <linearGradient id="bandBack" x1="0" y1="0" x2="1" y2="0">
          <stop offset="0" stop-color="var(--blue-light)"/>
          <stop offset="1" stop-color="var(--blue)"/>
        </linearGradient>
      </defs>
      <path d="M0 0 H700 V40 Q360 70 0 170 Z" fill="url(#bandBack)"/>
      <path d="M0 170 Q360 70 700 40 L700 48 Q360 82 0 180 Z" fill="var(--orange)"/>
    </svg>
    <p class="band-text band-text--web">www.meadowlarkpetcare.com.au</p>
    <div class="brand">
      <p class="brand-name">MEADOWLARK<br>PET CARE</p>
    </div>
  </section>

  <section class="card card--front" aria-label="Card front">
    <svg class="card-band" viewBox="0 0 700 400" aria-hidden="true">
      <defs>
        <linearGradient id="bandFront" x1="0" y1="0" x2="1" y2="0">
          <stop offset="0" stop-color="var(--blue)"/>
          <stop offset=".5" stop-color="var(--blue-light)"/>
          <stop offset="1" stop-color="var(--blue)"/>
        </linearGradient>
      </defs>
      <path d="M0 0 H700 V140 Q420 60 0 115 Z" fill="url(#bandFront)"/>
      <path d="M0 115 Q420 60 700 140 L700 150 Q420 72 0 123 Z" fill="var(--orange)"/>
    </svg>
    <p class="band-text band-text--title">Dana Kovich | Owner</p>
    <div class="brand">
      <p class="brand-name">MEADOWLARK PET CARE</p>
    </div>
    <div class="contacts">
      <div class="contact-row">
        <span class="contact">
          <svg class="contact-icon" viewBox="0 0 18 18" aria-hidden="true"><circle cx="9" cy="9" r="9" fill="var(--blue)"/><path d="M9 4a3 3 0 0 0-3 3c0 2.3 3 6 3 6s3-3.7 3-6a3 3 0 0 0-3-3z" fill="var(--white)"/></svg>
          Suite # 14, Elm Court, NSW 2150
        </span>
      </div>
      <div class="contact-row">
        <span class="contact">
          <svg class="contact-icon" viewBox="0 0 18 18" aria-hidden="true"><circle cx="9" cy="9" r="9" fill="var(--blue)"/><path d="M6 4.5l2 2-1 1.2a6 6 0 0 0 3.3 3.3l1.2-1 2 2-1.3 1.4C9.5 13 5 8.5 4.6 5.8z" fill="var(--white)"/></svg>
          0452716093
        </span>
        <span class="contact">
          <svg class="contact-icon" viewBox="0 0 18 18" aria-hidden="true"><circle cx="9" cy="9" r="9" fill="var(--blue)"/><rect x="6.5" y="4" width="5" height="10" rx="1" fill="var(--white)"/></svg>
          0452716094
        </span>
        <span class="contact">
          <svg class="contact-icon" viewBox="0 0 18 18" aria-hidden="true"><circle cx="9" cy="9" r="9" fill="var(--blue)"/><circle cx="9" cy="9" r="4.5" fill="none" stroke="var(--white)" stroke-width="1.2"/><path d="M4.5 9h9M9 4.5v9" stroke="var(--white)" stroke-width="1"/></svg>
          www.meadowlarkpetcare.com.au
        </span>
      </div>
      <div class="contact-row">
        <span class="contact">
          <svg class="contact-icon" viewBox="0 0 18 18" aria-hidden="true"><circle cx="9" cy="9" r="9" fill="var(--blue)"/><rect x="4.5" y="6" width="9" height="6" fill="var(--white)"/><path d="M4.5 6l4.5 3.5L13.5 6" fill="none" stroke="var(--blue)" stroke-width="1"/></svg>
          dana@meadowlarkpetcare.com.au
        </span>
        <span class="contact">
          <svg class="contact-icon" viewBox="0 0 18 18" aria-hidden="true"><circle cx="9" cy="9" r="9" fill="var(--blue)"/><rect x="5" y="7" width="8" height="5" fill="var(--white)"/><rect x="6.5" y="4.5" width="5" height="2.5" fill="var(--white)"/></svg>
          0297315820
        </span>
      </div>
    </div>
  </section>

</main>
</body>
</html>
```